Verdant Mist Irrigation LLC Business Card

Ok, first off let me thank you for taking the time to participate in this project !! I have my business logo that I want incorporated into business card design . My irrigation business is located in a very upscale part of town and we do high end homes . So with that said I'm planning on these cards being plastic credit card type cards. I would like them to be two sided . I'm thinking something bold , yet classy and clean . Not too busy . We do different types of work . 80% irrigation service and installation . 15% landscape lighting and the other 5% drainage and hardscapes ! I have a website that I want listed on it as well as our address , phone number and of course my name and title .
Updates

Target Market(s)

Upscale homeowners and architects

Industry/Entity Type

Landscape

Requirements
Must have
• Company logo, website, address , phone number , name , title , services offered

Www.VerdantMistIrrigation-demo.com
Marcus Hollen owner
205-555-0148
Verdant Mist Irrigation LLC
P.O. Box 947215
Birmingham, Alabama 35290

```html
<!DOCTYPE html>
<html lang="en">
<head>
<meta charset="utf-8">
<title>Verdant Mist Irrigation LLC – Business Cards</title>
<link rel="stylesheet" href="https://fonts.googleapis.com/css2?family=Source+Sans+3:wght@400;700&display=swap">
<style>
  :root {
    --stage: #33332b;
    --stage-edge: #1f1f1a;
    --white: #ffffff;
    --black: #000000;
    --leaf-green: #7ac943;
    --rule-green: #6cc93a;
    --blue-deep: #1668cf;
    --blue-light: #4fb6ef;
    --sky-top: #1b78d6;
    --sky-bottom: #5dd3e9;
    --silver: #e4e7eb;
    --mark-blue: #2a8fe0;
  }
  * { box-sizing: border-box; margin: 0; padding: 0; }
  html, body {
    width: 1200px; height: 839px; overflow: hidden;
    background: var(--stage);
    font-family: "Source Sans 3", "Myriad Pro", sans-serif;
  }
  .stage {
    position: relative; width: 1200px; height: 839px;
    border: 1px solid var(--stage-edge);
  }
  .card {
    position: absolute; width: 494px; height: 282px;
    border-radius: 28px; overflow: hidden;
  }
  .card--front-light { left: 72px; top: 108px; background: var(--white); }
  .card--back-light  { left: 633px; top: 108px; background: var(--white); }
  .card--front-dark  { left: 84px; top: 457px; background: var(--black); }
  .card--back-sky    { left: 645px; top: 457px;
    background: linear-gradient(180deg, var(--sky-top), var(--sky-bottom)); }

  .brand {
    position: absolute; left: 0; right: 0;
    display: flex; flex-direction: column; align-items: center;
  }
  .brand__dot { border-radius: 50%; background: var(--mark-blue); }
  .brand__name {
    font-weight: 700; color: var(--leaf-green);
    white-space: nowrap; line-height: 1;
  }
  .brand__services {
    margin-top: 14px; font-size: 14px; letter-spacing: 0.5px;
    white-space: nowrap; color: var(--blue-deep);
  }
  .card--front-light .brand, .card--front-dark .brand { top: 17px; }
  .card--front-light .brand__dot, .card--front-dark .brand__dot { width: 80px; height: 80px; margin-bottom: 7px; }
  .card--front-light .brand__name, .card--front-dark .brand__name { font-size: 29px; }

  .card--back-light .brand, .card--back-sky .brand { top: 50px; }
  .card--back-light .brand__dot, .card--back-sky .brand__dot { width: 114px; height: 114px; margin-bottom: 10px; }
  .card--back-light .brand__name, .card--back-sky .brand__name { font-size: 36px; }
  .card--back-sky .brand__dot { background: var(--silver); }
  .card--back-sky .brand__name { color: var(--silver); }
  .card--back-sky .brand__services { color: var(--white); }

  .holder {
    position: absolute; left: 0; right: 0; top: 166px;
    text-align: center; color: var(--white); font-size: 16px;
  }
  .holder__sep { margin: 0 6px; }

  .rule {
    position: absolute; left: 0; right: 0; height: 5px; background: var(--rule-green);
  }
  .card--front-light .rule { top: 188px; }
  .card--front-dark .rule { top: 187px; }

  .contact {
    position: absolute; left: 0; right: 0; bottom: 0;
    background: linear-gradient(180deg, var(--blue-deep), var(--blue-light));
    color: var(--white); font-size: 14.5px; line-height: 23.5px;
    padding: 8px 30px 0 22px;
    display: flex; justify-content: space-between;
  }
  .card--front-light .contact { top: 193px; }
  .card--front-dark .contact { top: 192px; }
  .contact__right { text-align: right; padding-top: 23.5px; }
  .contact__phone { display: inline-flex; align-items: center; gap: 4px; }
  .contact__phone svg { width: 11px; height: 14px; }
</style>
</head>
<body>
<main class="stage">

  <section class="card card--front-light">
    <div class="brand">
      <span class="brand__dot"></span>
      <span class="brand__name">Verdant Mist Irrigation</span>
    </div>
    <div class="rule"></div>
    <div class="contact">
      <div class="contact__left">
        <p>Verdant Mist Irrigation LLC</p>
        <p>P.O. Box 947215</p>
        <p>Birmingham, Alabama 35290</p>
      </div>
      <div class="contact__right">
        <p class="contact__phone"><svg viewBox="0 0 11 14"><path d="M3 0.5 L5 3.5 L3.6 5 C4.2 7 5.3 8.6 6.6 9.8 L8.2 8.7 L10.5 11 L8.5 13.5 C4 12 1.2 7 1 2 Z" fill="var(--leaf-green)"/></svg>205-555-0148</p>
        <p>Www.VerdantMistIrrigation-demo.com</p>
      </div>
    </div>
  </section>

  <section class="card card--back-light">
    <div class="brand">
      <span class="brand__dot"></span>
      <span class="brand__name">Verdant Mist Irrigation</span>
      <span class="brand__services">Irrigation · Landscape Lighting · Drainage &amp; Hardscapes</span>
    </div>
  </section>

  <section class="card card--front-dark">
    <div class="brand">
      <span class="brand__dot"></span>
      <span class="brand__name">Verdant Mist Irrigation</span>
    </div>
    <p class="holder">Marcus Hollen<span class="holder__sep">|</span>owner</p>
    <div class="rule"></div>
    <div class="contact">
      <div class="contact__left">
        <p>Verdant Mist Irrigation LLC</p>
        <p>P.O. Box 947215</p>
        <p>Birmingham, Alabama 35290</p>
      </div>
      <div class="contact__right">
        <p class="contact__phone"><svg viewBox="0 0 11 14"><path d="M3 0.5 L5 3.5 L3.6 5 C4.2 7 5.3 8.6 6.6 9.8 L8.2 8.7 L10.5 11 L8.5 13.5 C4 12 1.2 7 1 2 Z" fill="var(--leaf-green)"/></svg>205-555-0148</p>
        <p>Www.VerdantMistIrrigation-demo.com</p>
      </div>
    </div>
  </section>

  <section class="card card--back-sky">
    <div class="brand">
      <span class="brand__dot"></span>
      <span class="brand__name">Verdant Mist Irrigation</span>
      <span class="brand__services">Irrigation · Landscape Lighting · Drainage &amp; Hardscapes</span>
    </div>
  </section>

</main>
</body>
</html>
```